New Business Card Design Project LORVANTI-Italy

we are LORVANTI-Italy
our company in the market for 3 years we are luxury cosmetic company and its about time for a facelift :)
i will like to have elegant luxurious and unique business card
that will give the person that get it a unique, luxurious and elegant impression
I'm VERY OPEN FOR NEW IDEAS , even duo i add a few files of things that i see on line and i like them

i add my logo as well
my website is LORVANTI.COM
(if you would like to see the main style that we have)

Target Market(s)

adult that have money :)

Industry/Entity Type

Business

Contact Information for Business Card

Name - Dario Lorvanti
Position - CEO and CO Founder
address - 4817 E Halvern
telephone - 555-384-1926
email - dario@lorvanti.com
fax - 555-384-1926
website - LORVANTI.COM

Colors
000000
959595
fbee3e
ffffff

Requirements
Must have
• big logo in GOLD color
• elegant look
• impressive
Nice to have
• not must but maybe classy pattern background
• not must but maybe emblem
• maybe clear plastic business card
Should not have
• colors
• images

```html
<!DOCTYPE html>
<html lang="en">
<head>
<meta charset="utf-8">
<title>LORVANTI Italy – Business Card</title>
<link rel="stylesheet" href="https://fonts.googleapis.com/css2?family=Cormorant+Garamond:wght@500&family=Roboto:wght@400;500&display=swap">
<style>
  :root {
    --backdrop: #2b2b2b;
    --card-white: #f4f4f3;
    --gold: #d2ac45;
    --gold-light: #dfc462;
    --gold-deep: #d1aa48;
    --gold-faint: rgba(214, 180, 90, 0.14);
    --text-grey: #4a4a4a;
    --rule-grey: #8c8c8c;
    --white: #ffffff;
  }
  * { margin: 0; padding: 0; box-sizing: border-box; }
  html, body {
    width: 1200px;
    height: 960px;
    overflow: hidden;
    background: var(--backdrop);
  }
  .card {
    position: absolute;
    width: 600px;
    height: 342px;
    border-radius: 18px;
    overflow: hidden;
  }
  .card--front { left: 314px; top: 114px; background: var(--card-white); }
  .card--back {
    left: 311px; top: 473px;
    background: radial-gradient(ellipse at 50% 50%, var(--gold-light) 0%, var(--gold-deep) 80%);
  }

  .abs { position: absolute; }

  /* faint backdrop disc on front */
  .front-disc {
    left: 299px; top: 27px;
    width: 310px; height: 310px;
    border-radius: 50%;
    background: var(--gold-faint);
  }

  /* brand block */
  .brand-circle {
    border-radius: 50%;
    border: 2px solid var(--gold);
  }
  .front .brand-circle { left: 80px; top: 30px; width: 80px; height: 80px; }
  .brand-name {
    font-family: "Cormorant Garamond", serif;
    font-weight: 500;
    text-align: center;
    line-height: 1;
    white-space: nowrap;
  }
  .brand-rule { height: 2px; }
  .brand-country {
    font-family: "Cormorant Garamond", serif;
    font-weight: 500;
    text-align: center;
    line-height: 1;
    letter-spacing: 1px;
  }

  .card--front .brand-name { left: 31px; width: 178px; top: 128px; font-size: 36px; color: var(--gold); }
  .card--front .brand-rule { left: 31px; width: 178px; top: 168px; background: var(--gold); }
  .card--front .brand-country { left: 31px; width: 178px; top: 176px; font-size: 14px; color: var(--gold); }

  .person-name {
    right: 30px; top: 182px;
    font-family: "Roboto", sans-serif; font-weight: 500;
    font-size: 22px; color: var(--gold); line-height: 1;
  }
  .person-role {
    right: 30px; top: 209px;
    font-family: "Roboto", sans-serif; font-size: 15px;
    color: var(--text-grey); line-height: 1;
  }
  .divider { left: 33px; width: 537px; top: 236px; height: 1px; background: var(--rule-grey); }

  .contact-list {
    left: 32px; top: 252px;
    list-style: none;
    font-family: "Roboto", sans-serif; font-size: 14px; color: var(--text-grey);
  }
  .contact-list li { display: flex; align-items: center; height: 23px; }
  .contact-list svg { width: 16px; height: 14px; margin-right: 7px; fill: var(--gold); }

  .address-block {
    right: 30px; top: 273px;
    text-align: right;
    font-family: "Roboto", sans-serif; font-size: 14px; color: var(--text-grey);
    line-height: 24px;
  }

  /* back */
  .card--back .brand-circle { left: 254px; top: 83px; width: 92px; height: 92px; border-color: var(--white); }
  .card--back .brand-name { left: 190px; width: 220px; top: 197px; font-size: 42px; color: var(--white); }
  .card--back .brand-rule { left: 197px; width: 207px; top: 242px; background: var(--white); border-radius: 1px; }
  .card--back .brand-country { left: 190px; width: 220px; top: 253px; font-size: 15px; color: var(--white); }
  .back-web {
    left: 0; width: 600px; top: 288px;
    text-align: center;
    font-family: "Roboto", sans-serif; font-size: 15px;
    letter-spacing: 3px; color: var(--white);
  }
</style>
</head>
<body>

<section class="card card--front front" aria-label="Card front">
  <div class="abs front-disc" aria-hidden="true"></div>
  <div class="abs brand-circle" aria-hidden="true"></div>
  <div class="abs brand-name">LORVANTI</div>
  <div class="abs brand-rule"></div>
  <div class="abs brand-country">ITALY</div>

  <div class="abs person-name">DARIO LORVANTI</div>
  <div class="abs person-role">CEO &amp; CO Founder</div>
  <div class="abs divider"></div>

  <ul class="abs contact-list">
    <li>
      <svg viewBox="0 0 16 14" aria-label="Phone"><path d="M3 0.5 L5.5 0.5 L6.5 3.5 L5 5 C6 7.2 7.8 9 10 10 L11.5 8.5 L14.5 9.5 L14.5 12 C14.5 13 13.5 13.6 12.5 13.5 C6.8 12.8 2.2 8.2 1.5 2.5 C1.4 1.5 2 0.5 3 0.5 Z"/></svg>
      555-384-1926
    </li>
    <li>
      <svg viewBox="0 0 16 14" aria-label="Fax"><rect x="4" y="0.5" width="8" height="4"/><rect x="0.5" y="5" width="15" height="6" rx="1"/><rect x="4" y="9" width="8" height="4.5" fill="#f4f4f3" stroke="#d2ac45" stroke-width="1"/></svg>
      555-384-1926
    </li>
    <li>
      <svg viewBox="0 0 16 14" aria-label="Email"><rect x="0.5" y="2" width="15" height="10" rx="1"/><path d="M1 3 L8 8 L15 3" fill="none" stroke="#f4f4f3" stroke-width="1.2"/></svg>
      dario@lorvanti.com
    </li>
  </ul>

  <div class="abs address-block">
    <div>4817 E Halvern</div>
    <div>WWW.LORVANTI.COM</div>
  </div>
</section>

<section class="card card--back" aria-label="Card back">
  <div class="abs brand-circle" aria-hidden="true"></div>
  <div class="abs brand-name">LORVANTI</div>
  <div class="abs brand-rule"></div>
  <div class="abs brand-country">ITALY</div>
  <div class="abs back-web">www.lorvanti.com</div>
</section>

</body>
</html>
```